Business Card Design

We need a business card designed for our new company. Prefer a black card with white logo & writing.

Contact Information for Business Card

Ted Galloway, address: 7-4812 Fernhollow Road, Abbotsford, BC, V3K 8R2, Office Phone: 604-712-3390, Cell: 604-947-2164, Email: ted@resinworkshub.ca

Colors

Designer to choose only greyscale colors for use in the design.

```html
<!DOCTYPE html>
<html lang="en">
<head>
<meta charset="utf-8">
<title>Resin Works Hub — Business Card</title>
<link href="https://fonts.googleapis.com/css2?family=Montserrat:wght@400;600;700;800&display=swap" rel="stylesheet">
<style>
  :root {
    --stage: #2b2b2b;
    --card: #1f1f1f;
    --ink: #ffffff;
    --ink-soft: #cfcfcf;
    --scenery-light: rgba(255,255,255,0.16);
    --scenery-clear: rgba(255,255,255,0);
  }
  * { margin: 0; padding: 0; box-sizing: border-box; }
  html, body { width: 1200px; height: 1200px; overflow: hidden; }
  body {
    background: var(--stage);
    font-family: "Montserrat", Arial, sans-serif;
    color: var(--ink);
    position: relative;
  }
  .card {
    position: absolute;
    left: 160px;
    width: 880px;
    height: 503px;
    background: var(--card);
    border-radius: 4px;
    box-shadow: 0 18px 40px rgba(0,0,0,0.45);
    overflow: hidden;
  }
  .card--contact { top: 62px; }
  .card--brand { top: 635px; }

  .brand-name {
    font-weight: 800;
    color: var(--ink);
    letter-spacing: 0.02em;
    text-transform: uppercase;
    white-space: nowrap;
  }
  .card--contact .brand-name {
    position: absolute;
    left: 56px;
    top: 58px;
    font-size: 30px;
  }

  .holder { position: absolute; left: 56px; top: 150px; }
  .holder__name { font-size: 28px; font-weight: 700; }
  .holder__role { font-size: 16px; font-weight: 400; color: var(--ink-soft); margin-top: 2px; }

  .contact-list {
    position: absolute;
    left: 56px;
    top: 262px;
    list-style: none;
  }
  .contact-list li {
    display: flex;
    align-items: center;
    gap: 16px;
    font-size: 19px;
    line-height: 1;
    height: 32px;
  }
  .contact-list svg { width: 16px; height: 16px; fill: var(--ink); flex: none; }

  .scenery {
    position: absolute;
    right: 0;
    bottom: 0;
    width: 470px;
    height: 190px;
    background: linear-gradient(to top left, var(--scenery-light) 0%, var(--scenery-clear) 75%);
  }
  .address {
    position: absolute;
    right: 64px;
    bottom: 52px;
    text-align: right;
    font-size: 17px;
    font-style: normal;
    line-height: 1.35;
  }

  .card--brand .brand-name {
    position: absolute;
    left: 0;
    right: 0;
    top: 50%;
    transform: translateY(-50%);
    text-align: center;
    font-size: 66px;
  }
</style>
</head>
<body>

  <section class="card card--contact">
    <div class="brand-name">Resin Works Hub</div>

    <div class="holder">
      <div class="holder__name">Ted Galloway</div>
      <div class="holder__role">owner</div>
    </div>

    <ul class="contact-list">
      <li>
        <svg viewBox="0 0 24 24"><path d="M6.6 10.8a15.1 15.1 0 0 0 6.6 6.6l2.2-2.2a1 1 0 0 1 1-.25 11.4 11.4 0 0 0 3.6.57 1 1 0 0 1 1 1V20a1 1 0 0 1-1 1A17 17 0 0 1 3 4a1 1 0 0 1 1-1h3.5a1 1 0 0 1 1 1c0 1.25.2 2.45.57 3.6a1 1 0 0 1-.25 1z"/></svg>
        604-712-3390
      </li>
      <li>
        <svg viewBox="0 0 24 24"><path d="M7 1h10a2 2 0 0 1 2 2v18a2 2 0 0 1-2 2H7a2 2 0 0 1-2-2V3a2 2 0 0 1 2-2zm0 3v14h10V4zm5 15.5a1.2 1.2 0 1 0 0 2.4 1.2 1.2 0 0 0 0-2.4z"/></svg>
        604-947-2164
      </li>
      <li>
        <svg viewBox="0 0 24 24"><path d="M2 5h20v14H2zm2 2v.5l8 5 8-5V7zm0 2.8V17h16V9.8l-8 5z"/></svg>
        ted@resinworkshub.ca
      </li>
      <li>
        <svg viewBox="0 0 24 24"><path d="M12 2a10 10 0 1 0 0 20 10 10 0 0 0 0-20zm6.9 9h-3a15 15 0 0 0-1.3-5.6A8 8 0 0 1 18.9 11zM12 4c.9 1.2 1.8 3.7 1.9 7h-3.8C10.2 7.7 11.1 5.2 12 4zM9.4 5.4A15 15 0 0 0 8.1 11h-3a8 8 0 0 1 4.3-5.6zM5.1 13h3a15 15 0 0 0 1.3 5.6A8 8 0 0 1 5.1 13zm6.9 7c-.9-1.2-1.8-3.7-1.9-7h3.8c-.1 3.3-1 5.8-1.9 7zm2.6-1.4a15 15 0 0 0 1.3-5.6h3a8 8 0 0 1-4.3 5.6z"/></svg>
        www.resinworkshub.ca
      </li>
    </ul>

    <div class="scenery" role="img" aria-label="Mountain ridge illustration in white along the lower right corner"></div>

    <address class="address">
      7-4812 Fernhollow Road,<br>
      Abbotsford, BC, V3K 8R2
    </address>
  </section>

  <section class="card card--brand">
    <div class="brand-name">Resin Works Hub</div>
  </section>

</body>
</html>
```